Redesign Fitness Photos for Facebook Ads Needed

We are a fun, energetic, group fitness facility that needs to have a few (3) photos doctored up and turned into ads for Facebook & Instagram.
I would like the photos to be doctored up so that they are clear, bright, energetic.  Feel free to manipulate the photos, backgrounds, cropping, cutting as needed.
I would like to include text on photos:
Pulsora
New Year
Challenge
* Fitness Training  * Nutritional Support * Motivation & Support
Join Now
The text should be roughly the size of the examples included in order to comply with facebooks text size requirements
I have included 3 examples of another gyms ads which I like how the images are eye catching and text is clearly visible and pops with color.
Although I have attached multiple images that can be used,  I am only looking for 3 completed designs to be used for ads.

You choose the images that you feel you can modify the best.
I look forward to seeing your design.
Thank you.

```html
<!DOCTYPE html>
<html lang="en">
<head>
<meta charset="utf-8">
<title>Pulsora New Year Challenge Ad</title>
<link rel="stylesheet" href="https://fonts.googleapis.com/css2?family=Montserrat:ital,wght@0,800;1,900&family=Saira+Extra+Condensed:wght@500&display=swap">
<style>
  :root {
    --lime: #a8f50e;
    --black: #000000;
    --white: #ffffff;
    --backdrop: #bababa;
    --photo-dark: #0b0d08;
    --photo-glow: #3d6a0e;
    --outline-fill: #10130c;
  }
  * { margin: 0; padding: 0; box-sizing: border-box; }
  html, body { width: 1089px; height: 1200px; overflow: hidden; background: var(--backdrop); }
  .canvas { position: relative; width: 1089px; height: 1200px; }
  .ad {
    position: absolute; left: 24px; top: 80px;
    width: 767px; height: 767px;
    transform: scale(1.356); transform-origin: 0 0;
    background: var(--black); overflow: hidden;
    box-shadow: 0 4px 10px rgba(0,0,0,.25);
  }
  .ad__photo {
    position: absolute; inset: 0;
    background:
      radial-gradient(ellipse 240px 420px at 660px 470px, rgba(168,245,14,.32), transparent 70%),
      radial-gradient(ellipse 190px 150px at 610px 220px, #b87f5e 0%, transparent 75%),
      linear-gradient(100deg, var(--photo-dark) 35%, #1a1f14 58%, var(--photo-glow) 100%);
  }
  .ad__torn { position: absolute; left: 0; top: 0; width: 767px; height: 767px; }
  .brand { position: absolute; left: 48px; top: 30px; text-align: center; }
  .brand__name {
    font-family: "Montserrat", sans-serif; font-weight: 800;
    font-size: 40px; color: var(--black); line-height: 1; letter-spacing: -1px;
  }
  .brand__tagline {
    font-family: "Montserrat", sans-serif; font-weight: 800;
    font-size: 10px; letter-spacing: 1.8px; color: var(--black); margin-top: 2px;
  }
  .headline {
    position: absolute; left: 0; top: 0;
    font-family: "Montserrat", sans-serif; font-weight: 900; font-style: italic;
    font-size: 60px; line-height: 1; text-transform: uppercase;
  }
  .headline__line { position: absolute; white-space: nowrap; }
  .headline__brand { left: 34px; top: 358px; color: var(--white); }
  .headline__year { left: 124px; top: 418px; color: var(--lime); }
  .headline__challenge { left: 216px; top: 478px; color: var(--white); }
  .headline__outline {
    color: var(--outline-fill);
    text-shadow:
      -1.5px 0 0 var(--lime), 1.5px 0 0 var(--lime),
      0 -1.5px 0 var(--lime), 0 1.5px 0 var(--lime),
      -1px -1px 0 var(--lime), 1px -1px 0 var(--lime),
      -1px 1px 0 var(--lime), 1px 1px 0 var(--lime);
  }
  .services {
    position: absolute; left: 34px; top: 548px; width: 440px;
    font-family: "Saira Extra Condensed", sans-serif; font-weight: 500;
    font-size: 27px; letter-spacing: 1px; color: var(--white);
    text-align: center; line-height: 35px; text-transform: uppercase;
    white-space: nowrap;
  }
  .cta { position: absolute; left: 118px; top: 640px; width: 218px; height: 48px; }
  .cta__shape { position: absolute; inset: 0; }
  .cta__label {
    position: absolute; inset: 0; display: flex; align-items: center; justify-content: center;
    font-family: "Montserrat", sans-serif; font-weight: 900; font-style: italic;
    font-size: 25px; color: var(--black); text-transform: uppercase;
  }
</style>
</head>
<body>
<div class="canvas">
  <div class="ad">
    <div class="ad__photo" role="img" aria-label="Woman in a black tank top swinging a kettlebell in a dark gym, with lime halftone glow behind her"></div>
    <svg class="ad__torn" viewBox="0 0 767 767" aria-hidden="true">
      <path fill="var(--lime)" d="M0 0 H520 L505 8 L470 12 L445 30 L405 36 L382 58 L345 62 L322 80 L296 76 L270 100 L240 106 L214 118 L180 112 L150 124 L118 130 L95 150 L60 156 L30 170 L12 188 L0 196 Z"/>
    </svg>
    <div class="brand">
      <div class="brand__name">Pulsora</div>
      <div class="brand__tagline">Personal Group Training</div>
    </div>
    <h1 class="headline">
      <span class="headline__line headline__brand">Pulsora</span>
      <span class="headline__line headline__year">New Year</span>
      <span class="headline__line headline__challenge">Challe<span class="headline__outline">nge</span></span>
    </h1>
    <p class="services">Fitness Training | Nutritional Support<br>Motivation &amp; Support</p>
    <div class="cta">
      <svg class="cta__shape" viewBox="0 0 218 48" aria-hidden="true">
        <path fill="var(--lime)" d="M10 6 L200 3 L214 10 L204 16 L216 24 L206 32 L212 40 L196 46 L18 45 L4 40 L12 32 L0 24 L10 17 L2 10 Z"/>
      </svg>
      <span class="cta__label">Join Now</span>
    </div>
  </div>
</div>
</body>
</html>
```